SkyvornQ Business Cards and Stationary Design

Need a design for our business cards and stationary. I want to carry on the theme of the logo. I want the business cards to have a design on the back. I would like the business cards and the stationary to carry the same theme, design scheme, and branding

Target Market(s)

Airlines and Maintenance Facilities

Industry/Entity Type

Aviation

Contact Information for Business Card

Name
Position Title
Address: 4827 Trellis Hollow Road, Linden Cove, Marisola, 34951
Office Number
Mobile Number
Email
Website

Font styles to use
Serif
Sans Serif

Colors

Designer to choose colors to be used in the design.

```html
<!DOCTYPE html>
<html lang="en">
<head>
<meta charset="utf-8">
<title>SkyvornQ Business Card</title>
<link href="https://fonts.googleapis.com/css2?family=Roboto:wght@400;500;700&display=swap" rel="stylesheet">
<style>
  :root {
    --backdrop: #2b2b2d;
    --paper: #f2f2f2;
    --navy: #0b2a55;
    --navy-deep: #08244a;
    --sky: #1e9be0;
    --text-grey: #4d4d4d;
    --rule: #b8b8b8;
    --white: #ffffff;
  }
  * { margin: 0; padding: 0; box-sizing: border-box; }
  html, body { width: 1200px; height: 960px; overflow: hidden; }
  body {
    background: var(--backdrop);
    font-family: "Roboto", Arial, sans-serif;
    position: relative;
  }
  .card {
    position: absolute;
    width: 600px;
    height: 343px;
    border-radius: 18px;
    overflow: hidden;
  }
  .card-front { left: 314px; top: 113px; background: var(--paper); }
  .card-back { left: 311px; top: 472px; background: var(--navy-deep); }

  .brand-front {
    position: absolute; left: 60px; top: 115px; width: 244px;
    text-align: center;
  }
  .brand-mark {
    display: block; margin: 0 auto 14px;
    width: 72px; height: 72px; border-radius: 50%;
    border: 6px solid var(--sky);
  }
  .brand-name {
    font-weight: 700; font-size: 28px; letter-spacing: 3px;
    color: var(--navy); line-height: 1;
  }
  .divider {
    position: absolute; left: 323px; top: 82px;
    width: 1px; height: 186px; background: var(--rule);
  }
  .details { position: absolute; left: 352px; top: 84px; }
  .person-name { font-size: 22px; font-weight: 700; color: var(--navy); line-height: 1.1; }
  .person-title { font-size: 15px; font-weight: 500; color: var(--sky); margin-top: 2px; }
  .address { font-size: 14.5px; color: var(--text-grey); line-height: 18px; margin-top: 8px; }
  .contacts { list-style: none; margin-top: 10px; }
  .contacts li {
    display: flex; align-items: center; gap: 9px;
    font-size: 14.5px; color: var(--text-grey); line-height: 19.5px;
  }
  .contacts svg { width: 14px; height: 14px; fill: var(--navy); flex: none; }

  .edge-band {
    position: absolute; left: 0; bottom: 0; width: 100%; height: 16px;
    background: linear-gradient(90deg, var(--navy) 0%, var(--sky) 40%, #1580c8 56%, var(--navy) 56%);
  }
  .edge-slash {
    position: absolute; left: 338px; bottom: 0; width: 3px; height: 20px;
    background: var(--white); transform: skewX(-18deg);
  }

  .back-mark {
    position: absolute; left: 240px; top: 78px;
    width: 120px; height: 120px; border-radius: 50%;
    border: 13px solid var(--white);
  }
  .back-name {
    position: absolute; left: 0; width: 100%; top: 220px;
    text-align: center; font-weight: 700; font-size: 30px;
    letter-spacing: 4px; color: var(--white);
  }
  .back-web {
    position: absolute; left: 0; width: 100%; top: 289px;
    text-align: center; font-size: 14px; letter-spacing: 5.5px;
    color: var(--white);
  }
</style>
</head>
<body>
  <section class="card card-front">
    <div class="brand-front">
      <span class="brand-mark"></span>
      <div class="brand-name">SKYVORNQ</div>
    </div>
    <div class="divider"></div>
    <div class="details">
      <div class="person-name">MARCUS HALE</div>
      <div class="person-title">CEO/FOUNDER</div>
      <div class="address">4827 Trellis Hollow Road<br>Linden Cove, Marisola, 34951</div>
      <ul class="contacts">
        <li><svg viewBox="0 0 24 24"><path d="M6.6 10.8a15.1 15.1 0 0 0 6.6 6.6l2.2-2.2a1 1 0 0 1 1-.25 11.4 11.4 0 0 0 3.6.57 1 1 0 0 1 1 1V20a1 1 0 0 1-1 1A17 17 0 0 1 3 4a1 1 0 0 1 1-1h3.5a1 1 0 0 1 1 1c0 1.25.2 2.45.57 3.57a1 1 0 0 1-.25 1z"/></svg>772 555 0148</li>
        <li><svg viewBox="0 0 24 24"><path d="M7 1h10a2 2 0 0 1 2 2v18a2 2 0 0 1-2 2H7a2 2 0 0 1-2-2V3a2 2 0 0 1 2-2zm0 3v14h10V4zm5 15.5a1 1 0 1 0 0 2 1 1 0 0 0 0-2z"/></svg>772 555 0193</li>
        <li><svg viewBox="0 0 24 24"><path d="M2 5h20v14H2zm2 2v.5l8 5 8-5V7zm0 3v7h16v-7l-8 5z"/></svg>info@skyvornq.com</li>
        <li><svg viewBox="0 0 24 24"><path d="M12 2a10 10 0 1 0 0 20 10 10 0 0 0 0-20zm-1 17.9A8 8 0 0 1 4.2 10L9 14.8v1a2 2 0 0 0 2 2zm6.9-2.5A2 2 0 0 0 16 16h-1v-3a1 1 0 0 0-1-1H8v-2h2a1 1 0 0 0 1-1V7h2a2 2 0 0 0 2-2v-.4a8 8 0 0 1 2.9 12.8z"/></svg>www.skyvornq.com</li>
      </ul>
    </div>
    <div class="edge-band"></div>
    <div class="edge-slash"></div>
  </section>

  <section class="card card-back">
    <span class="back-mark"></span>
    <div class="back-name">SKYVORNQ</div>
    <div class="back-web">www.skyvornq.com</div>
  </section>
</body>
</html>
```